Residential Remodeling Contractor needs updated business card

I need a new design for my business card.
Name of the company is Ridgefell Construction. I need a card that commands presence, strength, integrity. I have been in business for 28 years. I am a Residential Remodeling Contractor that covers all aspects of a residential remodel and build.

```html
<!DOCTYPE html>
<html lang="en">
<head>
<meta charset="utf-8">
<title>Ridgefell Construction – Business Card</title>
<link href="https://fonts.googleapis.com/css2?family=Montserrat:wght@300;400;600&display=swap" rel="stylesheet">
<style>
  :root {
    --page-bg: #b3b3b3;
    --card-navy: #223d7c;
    --ink-white: #ffffff;
    --ink-soft: #dfe5f2;
    --rule: rgba(255,255,255,0.85);
  }
  * { box-sizing: border-box; margin: 0; padding: 0; }
  html, body {
    width: 1200px; height: 900px; overflow: hidden;
    background: var(--page-bg);
    font-family: "Montserrat", Arial, sans-serif;
    color: var(--ink-white);
  }
  .sheet {
    width: 1200px; height: 900px;
    display: flex; flex-direction: column; align-items: center; justify-content: center;
    gap: 40px;
  }
  .card {
    position: relative;
    width: 700px; height: 400px;
    background: var(--card-navy);
    box-shadow: 0 6px 18px rgba(0,0,0,0.25);
  }

  /* Front: contact side */
  .brand-name {
    position: absolute;
    font-weight: 400;
    letter-spacing: 0.08em;
    text-transform: uppercase;
    color: var(--ink-white);
    line-height: 1.1;
  }
  .card-front .brand-name {
    right: 70px; top: 60px;
    font-size: 30px;
    display: flex; align-items: center; gap: 14px;
  }
  .brand-mark {
    width: 16px; height: 16px; background: var(--ink-white); flex: none;
  }
  .card-front .rule {
    position: absolute; left: 40px; right: 40px; top: 208px;
    height: 1px; background: var(--rule);
  }
  .person {
    position: absolute; left: 50px; top: 140px;
  }
  .person-name { font-weight: 600; font-size: 30px; letter-spacing: 0.01em; }
  .person-role { font-weight: 300; font-size: 15px; margin-top: 4px; color: var(--ink-soft); }
  .contacts {
    position: absolute; left: 50px; top: 236px;
    list-style: none; display: flex; flex-direction: column; gap: 12px;
  }
  .contacts li {
    display: flex; align-items: center; gap: 14px;
    font-size: 17px; font-weight: 400;
  }
  .contacts svg { width: 20px; height: 20px; flex: none; }
  .address {
    position: absolute; right: 50px; bottom: 60px;
    text-align: right; font-size: 16px; font-weight: 400; line-height: 1.4;
    font-style: normal;
  }

  /* Back: brand side */
  .card-back { display: flex; align-items: center; justify-content: center; }
  .card-back .brand-name {
    position: static;
    font-size: 44px;
    display: flex; align-items: center; gap: 22px;
  }
  .card-back .brand-mark { width: 24px; height: 24px; }
</style>
</head>
<body>
<main class="sheet">
  <section class="card card-front" aria-label="Business card front">
    <div class="brand-name"><span class="brand-mark"></span><span>Ridgefell<br>Construction</span></div>
    <div class="person">
      <div class="person-name">Daniel Reeve</div>
      <div class="person-role">Owner</div>
    </div>
    <div class="rule"></div>
    <ul class="contacts">
      <li>
        <svg viewBox="0 0 20 20" aria-hidden="true"><path d="M5 2h3l1.5 4-2 1.5a10 10 0 0 0 5 5L14 10.5l4 1.5v3a2 2 0 0 1-2 2A14 14 0 0 1 3 4a2 2 0 0 1 2-2z" fill="#fff"/></svg>
        <span>555.014.2290</span>
      </li>
      <li>
        <svg viewBox="0 0 20 20" aria-hidden="true"><rect x="2" y="4" width="16" height="12" rx="1" fill="#fff"/><path d="M2.5 4.5 10 11l7.5-6.5" fill="none" stroke="#223d7c" stroke-width="1.5"/></svg>
        <span>info@ridgefellconstruction.com</span>
      </li>
      <li>
        <svg viewBox="0 0 20 20" aria-hidden="true"><circle cx="10" cy="10" r="8" fill="#fff"/><path d="M2 10h16M10 2c3 3 3 13 0 16M10 2c-3 3-3 13 0 16" fill="none" stroke="#223d7c" stroke-width="1.3"/></svg>
        <span>www.ridgefellconstruction.com</span>
      </li>
    </ul>
    <address class="address">42 Cedar Hollow Lane<br>Brookfield, MS 39000</address>
  </section>

  <section class="card card-back" aria-label="Business card back">
    <div class="brand-name"><span class="brand-mark"></span><span>Ridgefell<br>Construction</span></div>
  </section>
</main>
</body>
</html>
```